first fantastic look and impression

We are looking for a concept for letterhead, business card, emailfooter and template for invoices or offers for our company in the consultation business.
The dancer is a symbol who we are: it looks simple, but there is a lot of hard work and many years of training in this movement. The look is also what we want: elegant, modern, strong, with a touch of extravaganza
Target Market(s)
Hotelbusiness , Consulting
Font styles to use
Sans Serif
Other font styles liked:
- please give us a option we are open
Requirements
Must have
- We are not typical consultants but sparring partners and coaches for the hotel and that should also be expressed in the design. Maybe there is an icon that supports the whole thing. We are more modern and bolder than our industry colleagues.
we are modern, fresh, agile, fast
Nice to have
- a icon

```html
<!DOCTYPE html>
<html lang="en">
<head>
<meta charset="utf-8">
<title>Norvane Advisory business card</title>
<link href="https://fonts.googleapis.com/css2?family=Open+Sans:wght@400;600;700&display=swap" rel="stylesheet">
<style>
  :root {
    --backdrop: #1c1c1e;
    --card-dark: #151515;
    --card-light: #ffffff;
    --ink: #111111;
    --ink-soft: #555555;
    --silver: #c9c9cc;
    --rule: #333333;
  }
  * { margin: 0; padding: 0; box-sizing: border-box; }
  html, body {
    width: 1200px; height: 786px; overflow: hidden;
    background: var(--backdrop);
    font-family: "Open Sans", Arial, sans-serif;
  }
  .stage {
    position: relative; width: 1200px; height: 786px;
    display: flex; align-items: center; justify-content: center; gap: 60px;
  }
  .card {
    width: 510px; height: 292px; position: relative; flex: none;
    box-shadow: 0 16px 40px rgba(0,0,0,.45);
  }
  .card--front {
    background: var(--card-dark);
    display: flex; align-items: center; justify-content: center;
  }
  .card--back {
    background: var(--card-light);
    display: flex; align-items: center;
    padding: 0 30px 0 30px;
  }
  .wordmark {
    font-weight: 600; letter-spacing: 2px; text-transform: uppercase;
    white-space: nowrap;
  }
  .card--front .wordmark { color: var(--silver); font-size: 26px; }
  .card--back .wordmark { color: var(--ink); font-size: 17px; }
  .brand-block { width: 200px; flex: none; display: flex; justify-content: center; }
  .divider {
    width: 1px; height: 170px; margin: 0 24px 0 22px; flex: none;
    background: linear-gradient(var(--rule) 0 22%, transparent 22% 32%, var(--rule) 32% 100%);
  }
  .contact { color: var(--ink-soft); font-size: 12.5px; line-height: 1.45; white-space: nowrap; }
  .contact__name {
    color: var(--ink); font-weight: 700; font-size: 15px;
    text-transform: uppercase; letter-spacing: .3px;
  }
  .contact__role { font-weight: 600; margin-bottom: 14px; }
  .contact__address { margin-bottom: 4px; }
  .contact__line { display: flex; align-items: center; gap: 7px; }
  .contact__line svg { width: 11px; height: 11px; flex: none; }
</style>
</head>
<body>
<main class="stage">
  <section class="card card--front" aria-label="Card front">
    <span class="wordmark">Norvane Advisory</span>
  </section>

  <section class="card card--back" aria-label="Card back">
    <div class="brand-block">
      <span class="wordmark">Norvane Advisory</span>
    </div>
    <div class="divider"></div>
    <div class="contact">
      <div class="contact__name">Lena Marwick</div>
      <div class="contact__role">Managing Director</div>
      <div class="contact__address">48 Cedar Lane,<br>Oakridge, ON K2B 4T1</div>
      <div class="contact__line">
        <svg viewBox="0 0 12 12"><path d="M2.5 1 4.5 1 5.3 3.6 4 4.6a7 7 0 0 0 3.4 3.4l1-1.3 2.6.8v2c0 .6-.5 1-1 1A9.5 9.5 0 0 1 1.5 2c0-.5.4-1 1-1z" fill="#222"/></svg>
        <span>+15550142876</span>
      </div>
      <div class="contact__line">
        <svg viewBox="0 0 12 12"><rect x="1" y="2.5" width="10" height="7" fill="#222"/><path d="M1.3 2.8 6 6.6l4.7-3.8" fill="none" stroke="#fff" stroke-width=".9"/></svg>
        <span>info@norvaneadvisory.com</span>
      </div>
      <div class="contact__line">
        <svg viewBox="0 0 12 12"><g fill="none" stroke="#222" stroke-width="1"><circle cx="6" cy="6" r="4.8"/><ellipse cx="6" cy="6" rx="2" ry="4.8"/><path d="M1.2 6h9.6"/></g></svg>
        <span>www.norvaneadvisory.com</span>
      </div>
    </div>
  </section>
</main>
</body>
</html>
```